Church Website with Home Page and Member Sermon Library

I am in need of an updated design for our church website. This will include 4 pages (outlined below). We are a conservative, evangelical, Christian church. The site should be modern and clean, while still reflecting our conservative values. I already have a logo for our church, and I want the site to incorporate the logo, and match the logo/branding. Stock photos are allowed if needed, but I have uploaded some images of our church and would prefer those images to be used if possible. Any stock photos used should not include any people in the photos (scenery, nature, buildings, animals, etc. are fine).

The site will need 4 pages: Home, Support Us (Donate), Login, and Recording Library.

Page 1: Home
The home page should include the following sections:

- Navigation: Should include links to each section of the home page plus a "listen live" link which will take the user to a live-streaming site and a "support us" link which will take the user to a support/donate page.

- Announcements: Can be either a banner or some other design, but there needs to be some way for us to post announcements for visitors to see. I'm open for creative ideas in this section, but would like it not to take up a lot of room on the page.

- About Us: Should include address, service times (see attached document), and information about the church.

- Pastor Bio: A section that introduces our pastor and gives a short bio about our pastor. Would like this section to include a picture of our pastor. Somewhere in this section I would like to include this Bible reference: "And I will give you pastors according to mine heart, which shall feed you with knowledge and understanding. Jer 3:15 LPW"

- Articles of Faith (What We Believe): This should include several sub-sections each with a heading, body, and possibly 1 or more scripture references. I have attached a document to the brief that includes our articles of faith. Feel free to be creative with this section in how you lay these out and format them.

- Support Us: A small section that explains what kind of support someone can give and a link to a donation page. The link can say something like "Support Us" or "Donate Now".

- Contact form: A contact form that allows the visitor to send us a message. The contact form should ask for name, email, phone, and message.

- Footer: A footer that will be displayed on all pages of the site. This should include at a minimum a link to the home page (or a link to each individual section in the home page if you prefer), a link to "listen live", a link to "support us", a link to "contact us" (or you can put the contact form directly in the footer if you prefer), the address, and a "member login" link.

Page 2: Support Us
The donation page should include a form the visitor can fill out to make a donation. We will embed a third party form later. For this design, please just mock out the design with a basic form asking for name, phone, and email.

Page 3: Login
The recording library (detailed below) will require members to login with a shared numeric code before accessing the page. We need a design for a login screen. The screen should include navigation/footer just like all other pages, but the body of the login page will consist only of a form that asks the user to enter the access code and then a "login" button.

Page 4: Recording Library

The library page is a member-only page that will require a shared, numeric pass code to access. On this page, members will be able to access a filterable list of past sermons. The page by default should display most recent sermons, but should also include a search form that allows the member to filter the sermon list to find a particular sermon. The search form should allow the user to select a filter type (e.g. Speaker name, date, event, etc.) and type in a value to search. They should be able to add multiple filters and remove filters that have been added. Each sermon that is displayed in the result list should include basic information such as title, date, speaker, tags, etc. along with a download icon, and an embedded audio player where they can click a play button to stream it on-demand. Each sermon should also have clickable tags associated with it that can be used to find related sermons.
Updates

I have uploaded several images of our church. Feel free to incorporate these into your design if possible.

Target Market(s)

Church Members

Industry/Entity Type

Religion

Number of Pages Required

4 page

Font styles to use
Sans Serif

Colors

Designer to choose colors to be used in the design.

Requirements
Must have
• Must incorporate the logo (attached)
Nice to have
• Would like the design to incorporate pictures of our church (attached) instead of stock photos if possible.
Should not have
• Please avoid an overly cluttered design. Stock photos used should not include any people in the photos.

```html
<!DOCTYPE html>
<html lang="en">
<head>
<meta charset="utf-8">
<title>Grace Covenant Church</title>
<link href="https://fonts.googleapis.com/css2?family=Josefin+Sans:wght@400;600;700&family=Poppins:wght@400;500;600&family=Lora:wght@500;600&display=swap" rel="stylesheet">
<style>
:root{
  --green:#3d6b29;
  --green-dark:#2f5820;
  --green-soft:#5b8a3c;
  --teal:#17b3cc;
  --teal-dark:#0e97b0;
  --sky:#e8f6fa;
  --ink:#2b2b2b;
  --muted:#6d6d6d;
  --white:#ffffff;
  --line:#e3e3e3;
}
*{box-sizing:border-box;margin:0;padding:0}
html,body{width:1200px;height:4204px;overflow:hidden}
body{font-family:"Poppins",sans-serif;color:var(--ink);background:var(--white);position:relative;font-size:12px;line-height:1.6}
.section{position:absolute;left:0;width:1200px}
.heading{font-family:"Josefin Sans",sans-serif;font-weight:700;text-transform:uppercase;letter-spacing:1px}
.rule{width:60px;height:3px;background:var(--teal);margin:8px auto 0;border-radius:2px}
.btn{display:inline-flex;align-items:center;gap:8px;height:34px;padding:0 20px;border-radius:17px;font-size:11px;font-weight:600;color:var(--white);text-transform:uppercase;letter-spacing:.5px}
.btn-teal{background:var(--teal)}
.btn-green{background:var(--green)}
.btn .dot{width:16px;height:16px;border-radius:50%;background:rgba(255,255,255,.9)}
.photo{display:block}

/* header */
.site-header{top:0;height:620px;background:#f7f9f4}
.brand{position:absolute;left:60px;top:30px;font-family:"Josefin Sans",sans-serif;font-weight:700;color:var(--green);font-size:18px;line-height:1.1;text-transform:uppercase;letter-spacing:2px;text-align:center}
.nav{position:absolute;left:450px;top:44px;display:flex;gap:30px;font-size:11px;font-weight:600;text-transform:uppercase}
.nav a{color:var(--ink);text-decoration:none}
.nav a.active{color:var(--teal)}
.login{position:absolute;right:60px;top:34px}
.hero-title{position:absolute;top:120px;width:100%;text-align:center;color:var(--green);font-size:46px;line-height:1.05}
.hero-text{position:absolute;top:222px;left:390px;width:420px;text-align:center;font-size:13px;color:var(--muted)}
.hero-actions{position:absolute;top:275px;width:100%;display:flex;justify-content:center;gap:14px}
.hero-photo{position:absolute;top:330px;left:0;width:1200px;height:300px;background:linear-gradient(180deg,#d9e3ea 0%,#c7b6a3 45%,#9b6e55 70%,#7d7c62 100%)}

/* about */
.about{top:560px;height:700px}
.about-bg{position:absolute;top:0;left:0}
.about-title{position:absolute;top:140px;width:100%;text-align:center;color:var(--white);font-size:40px}
.about-title .rule{background:var(--white)}
.col-title{font-family:"Lora",serif;font-weight:600;color:var(--white);font-size:17px;margin-bottom:12px}
.col{position:absolute;top:230px}
.times-card{width:280px;height:250px;border-radius:10px;background:linear-gradient(160deg,#19b6c4 0%,#3aa88a 60%,#5c9a4a 100%);padding:22px 22px;color:var(--white)}
.time-row{display:flex;gap:12px;margin-bottom:16px;align-items:flex-start}
.time-row svg{flex:none;margin-top:3px}
.time-label{font-size:10px;opacity:.9}
.time-value{font-family:"Lora",serif;font-weight:600;font-size:14px;line-height:1.2}
.address{display:flex;gap:10px;color:var(--white);font-size:12px;margin-bottom:18px}
.address strong{display:block;font-family:"Lora",serif;font-size:13px;font-weight:600;text-transform:uppercase}
.map{width:300px;height:150px;border-radius:10px;background:linear-gradient(135deg,#eef1ec,#dfe6da)}
.about-text{width:300px;color:#e8f0e2;font-size:10.5px;margin-bottom:14px}
.about-photo{width:300px;height:150px;border-radius:8px;background:linear-gradient(180deg,#dde6ec 0%,#b38a70 55%,#7a8a5c 100%)}

/* pastor */
.pastor{top:1290px;height:540px}
.pastor-card{position:absolute;left:200px;top:20px;width:800px;height:480px;border:1px solid var(--line);border-radius:12px;background:var(--white)}
.pastor-photo{position:absolute;left:70px;top:-10px;width:300px;height:420px;border-radius:150px 150px 0 0;background:linear-gradient(180deg,#e9e4dc 0%,#b9a591 60%,#5a4336 100%)}
.badge{position:absolute;left:25px;top:170px;width:64px;height:64px;border-radius:50%;background:var(--green-soft);border:4px solid #d9edc9;color:var(--white);display:flex;align-items:center;justify-content:center;font-weight:600;font-size:16px}
.pastor-btn{position:absolute;left:210px;top:390px;height:34px;padding:0 22px;background:var(--white);border-radius:17px;box-shadow:0 4px 14px rgba(0,0,0,.12);display:flex;align-items:center;font-size:10px;font-weight:600;color:var(--green);text-transform:uppercase}
.pastor-body{position:absolute;left:430px;top:110px;width:320px}
.pastor-body h2{color:var(--green);font-size:36px;margin-bottom:18px}
.pastor-body p{font-size:10.5px;color:var(--muted);margin-bottom:14px}

/* articles */
.articles{top:1860px;height:660px}
.articles-bg{position:absolute;top:0;left:0}
.articles-title{position:absolute;top:110px;width:100%;text-align:center;color:var(--green);font-size:38px}
.believe{position:absolute;left:210px;top:200px;font-family:"Lora",serif;font-weight:600;font-size:18px;color:var(--ink)}
.faith-list{position:absolute;left:210px;top:236px;width:360px;list-style:none}
.faith-list li{height:40px;display:flex;align-items:center;justify-content:space-between;padding:0 14px 0 24px;border-bottom:1px solid #cfe3ea;font-family:"Lora",serif;font-weight:600;font-size:12px;color:var(--ink)}
.faith-list li.active{background:var(--green);color:var(--white);border-radius:0 20px 20px 0}
.faith-list li span.arrow{width:60px;height:1px;background:currentColor;position:relative}
.faith-list li span.arrow::after{content:"";position:absolute;right:0;top:-3px;border-left:6px solid currentColor;border-top:3.5px solid transparent;border-bottom:3.5px solid transparent}
.faith-photo{position:absolute;left:650px;top:215px;width:340px;height:210px;border-radius:8px;background:linear-gradient(180deg,#f1ede6 0%,#b69c83 50%,#6f5240 100%)}
.faith-chip{position:absolute;left:600px;top:270px;width:90px;height:90px;border-radius:10px;background:var(--white);box-shadow:0 6px 18px rgba(0,0,0,.12);display:flex;align-items:center;justify-content:center}
.faith-chip div{width:50px;height:50px;border-radius:8px;background:linear-gradient(135deg,#8fc46a,#1bb3c7)}
.faith-text{position:absolute;left:650px;top:440px;width:340px;font-size:10.5px;color:var(--muted)}

/* help */
.help{top:2520px;height:500px;background:var(--white)}
.help-photo{position:absolute;right:0;top:20px;width:640px;height:480px;border-radius:260px 0 0 260px;background:linear-gradient(180deg,#e4edf2 0%,#c9d3d9 50%,#8da1ae 100%)}
.help-title{position:absolute;left:60px;top:150px;color:var(--green);font-size:48px;line-height:1}
.help-sub{position:absolute;left:60px;top:210px;color:var(--green);font-size:24px;line-height:1.2;font-weight:600;font-family:"Josefin Sans",sans-serif;text-transform:uppercase}
.help-actions{position:absolute;left:60px;top:290px;display:flex;gap:12px}

/* contact */
.contact{top:3010px;height:660px}
.contact-bg{position:absolute;top:0;left:0}
.contact-title{position:absolute;top:120px;width:100%;text-align:center;color:var(--white);font-size:38px}
.contact-title .rule{background:var(--white)}
.form{position:absolute;left:210px;top:205px;width:780px;display:grid;grid-template-columns:1fr 1fr;gap:18px 20px}
.field{height:36px;border-radius:18px;background:var(--white);padding:0 18px;display:flex;align-items:center;font-size:10px;color:#9a9a9a}
.field.message{grid-column:1 / 3;height:130px;border-radius:16px;align-items:flex-start;padding-top:12px}
.submit{position:absolute;left:530px;top:550px}

/* footer */
.footer{top:3670px;height:330px}
.f-col{position:absolute;top:60px}
.f-col h4{font-family:"Lora",serif;font-weight:600;font-size:13px;text-transform:uppercase;margin-bottom:12px}
.f-col p,.f-col a{display:block;font-size:11px;color:var(--muted);text-decoration:none;line-height:1.8}
.f-brand{position:absolute;left:450px;top:70px;width:300px;text-align:center;font-family:"Josefin Sans",sans-serif;font-weight:700;color:var(--green);font-size:26px;line-height:1.1;letter-spacing:3px;text-transform:uppercase}
.f-btns{position:absolute;right:110px;top:60px;display:flex;flex-direction:column;gap:12px}
.copyright{position:absolute;top:230px;width:100%;text-align:center;font-size:10px;color:var(--muted)}
.footer-photo{top:4000px;height:204px;background:linear-gradient(180deg,#dfe8ef 0%,#c2a08a 45%,#8a5f48 70%,#7f8463 100%)}
</style>
</head>
<body>

<header class="section site-header">
  <div class="brand">Grace<br>Covenant<br>Church</div>
  <nav class="nav">
    <a href="#" class="active">Home</a>
    <a href="#">Support Us</a>
    <a href="#">Recordings Library</a>
  </nav>
  <a class="btn btn-teal login"><span class="dot"></span>Login</a>
  <h1 class="heading hero-title">God give us power<br>to believe Trinity</h1>
  <p class="hero-text">We believe in the God head bodily, known as the Divine Trinity. We are a conservative, evangelical, Christian church.</p>
  <div class="hero-actions">
    <a class="btn btn-teal"><span class="dot"></span>Listen Live</a>
    <a class="btn btn-green"><span class="dot"></span>Donate</a>
  </div>
  <div class="hero-photo photo" role="img" aria-label="Photo of the brick church building with its sign and lawn"></div>
</header>

<section class="section about">
  <svg class="about-bg" width="1200" height="700" viewBox="0 0 1200 700" aria-hidden="true">
    <path d="M0 70 Q600 0 1200 70 V640 Q600 700 0 640 Z" fill="var(--green)"/>
  </svg>
  <h2 class="heading about-title">About Us<div class="rule"></div></h2>

  <div class="col" style="left:110px">
    <div class="col-title">Service Times</div>
    <div class="times-card">
      <div class="time-row">
        <svg width="20" height="20" viewBox="0 0 20 20"><path d="M10 3 1 7.5 10 12 19 7.5Z M5 10v4c3 2 7 2 10 0v-4" fill="none" stroke="#fff" stroke-width="1.6"/></svg>
        <div><div class="time-label">Wednesday Evening Service</div><div class="time-value">7:30 PM Sunday School: 10:00 AM</div></div>
      </div>
      <div class="time-row">
        <svg width="20" height="20" viewBox="0 0 20 20"><circle cx="10" cy="10" r="8" fill="none" stroke="#fff" stroke-width="1.6"/><path d="M10 5v5l3 2" stroke="#fff" stroke-width="1.6" fill="none"/></svg>
        <div><div class="time-label">Sunday Morning Service</div><div class="time-value">11:00 AM Sunday</div></div>
      </div>
      <div class="time-row">
        <svg width="20" height="20" viewBox="0 0 20 20"><path d="M14 3a7 7 0 1 0 3 10 6 6 0 0 1-3-10Z" fill="none" stroke="#fff" stroke-width="1.6"/></svg>
        <div><div class="time-label">Evening Service</div><div class="time-value">6:00 PM</div></div>
      </div>
    </div>
  </div>

  <div class="col" style="left:445px">
    <div class="col-title">Location</div>
    <div class="address">
      <svg width="18" height="22" viewBox="0 0 18 22"><path d="M9 1a7 7 0 0 1 7 7c0 5-7 13-7 13S2 13 2 8a7 7 0 0 1 7-7Z" fill="var(--teal)"/><circle cx="9" cy="8" r="2.6" fill="#fff"/></svg>
      <div><strong>Grace Covenant Church</strong>2140 Cedar Hollow Rd, Ashford,<br>TN 37012</div>
    </div>
    <div class="map photo" role="img" aria-label="Street map showing the church location"></div>
  </div>

  <div class="col" style="left:790px">
    <div class="col-title">About Church</div>
    <p class="about-text">Our church family gathers each week to worship, pray and study the Word together. We hold to the old paths of faith and welcome every visitor who seeks the Lord with an open heart.</p>
    <div class="about-photo photo" role="img" aria-label="Photo of the church building from the side"></div>
  </div>
</section>

<section class="section pastor">
  <div class="pastor-card">
    <div class="pastor-photo photo" role="img" aria-label="Photo of the pastor standing at the pulpit"></div>
    <div class="badge">25</div>
    <div class="pastor-btn">Meet Our Pastor</div>
    <div class="pastor-body">
      <h2 class="heading">Our Pastor</h2>
      <p>Our pastor has faithfully served this congregation for many years, preaching the Word with conviction and caring for every family as a shepherd of the flock entrusted to him by God.</p>
      <p>"And I will give you pastors according to mine heart, which shall feed you with knowledge and understanding." Jer 3:15 LPW. He leads with prayer and humility each day.</p>
    </div>
  </div>
</section>

<section class="section articles">
  <svg class="articles-bg" width="1200" height="660" viewBox="0 0 1200 660" aria-hidden="true">
    <path d="M0 60 Q600 -10 1200 60 V660 H0 Z" fill="var(--sky)"/>
  </svg>
  <h2 class="heading articles-title">Articles of Faith<div class="rule"></div></h2>
  <div class="believe">What We Believe...</div>
  <ul class="faith-list">
    <li class="active">The God Head<span class="arrow"></span></li>
    <li>Sanctification<span class="arrow"></span></li>
    <li>Baptism of the Holy Ghost<span class="arrow"></span></li>
    <li>Divine Healing<span class="arrow"></span></li>
    <li>Second Coming of Christ<span class="arrow"></span></li>
    <li>Full Salvation<span class="arrow"></span></li>
    <li>Eternity<span class="arrow"></span></li>
  </ul>
  <div class="faith-photo photo" role="img" aria-label="Photo of the church sanctuary with pews and pulpit"></div>
  <div class="faith-chip" role="img" aria-label="Praying hands icon"><div></div></div>
  <p class="faith-text">We believe in the God head bodily, known as the Divine Trinity. The three are one: the Father, the Son and the Holy Ghost, each fully God, equal in power and glory.</p>
</section>

<section class="section help">
  <div class="help-photo photo" role="img" aria-label="Photo of the pastor preaching from an open Bible at the pulpit"></div>
  <h2 class="heading help-title">Bring Help &amp; Hope</h2>
  <div class="help-sub">To the people who depend and<br>believe in the God head</div>
  <div class="help-actions">
    <a class="btn btn-teal"><span class="dot"></span>Support Us</a>
    <a class="btn btn-green"><span class="dot"></span>Donate</a>
  </div>
</section>

<section class="section contact">
  <svg class="contact-bg" width="1200" height="660" viewBox="0 0 1200 660" aria-hidden="true">
    <path d="M0 60 Q600 0 1200 60 V580 L600 650 0 580 Z" fill="var(--green)"/>
  </svg>
  <h2 class="heading contact-title">Contact Us<div class="rule"></div></h2>
  <div class="form">
    <div class="field">First Name</div>
    <div class="field">Last Name</div>
    <div class="field">Email Address</div>
    <div class="field">Phone Number</div>
    <div class="field message">Message</div>
  </div>
  <a class="btn btn-teal submit">Submit Now</a>
</section>

<footer class="section footer">
  <div class="f-col" style="left:110px">
    <h4>Links</h4>
    <a href="#">Home</a><a href="#">Support Us</a><a href="#">Recording Library</a><a href="#">Login</a>
  </div>
  <div class="f-col" style="left:290px">
    <h4>Location</h4>
    <p>2140 Cedar Hollow Rd<br>Ashford, TN 37012</p>
  </div>
  <div class="f-brand">Grace<br>Covenant<br>Church</div>
  <div class="f-col" style="left:745px">
    <h4>Location</h4>
    <p>2140 Cedar Hollow Rd<br>Ashford, TN 37012</p>
  </div>
  <div class="f-btns">
    <a class="btn btn-teal"><span class="dot"></span>Listen Live</a>
    <a class="btn btn-green"><span class="dot"></span>Donate</a>
  </div>
  <p class="copyright">© 2024 Grace Covenant Church. All Rights Reserved.</p>
</footer>
<div class="section footer-photo photo" role="img" aria-label="Photo of the church building front"></div>

</body>
</html>
```